Business Card for Multi-Brand Sportswear Company

We are looking for a business card which represents our company and the multiple brands within it.

The company: Fen Athletics (LTD)
The brands: Fen, TavaPuni, ElmStretch, Grit and Rain

Employees using these cards would be representing Fen Athletics, rather than any of the individual brands. You will see a current design within the uploaded files, to give some inspiration. The actual text of the brands is not necessary, but the logos should be on there is some format.

Our creative minds on this are stretched, so we are looking for someone to make this their own, and show us what a good business card should look like.

We may like to get these printed with spot gloss, so keep that in mind with your designs.

www.fenathletics.co.uk

Industry/Entity Type

Business

Contact Information for Business Card

Leo Pemberton-Hale
Operations Manager
(+44) 1632 960 418
Leo@fenathletics.co.uk
www.fenathletics.co.uk

Font styles to use
Sans Serif
Other font styles liked:
• Eurostile

Colors
ffffff

Requirements
Nice to have
• Dark (black) background

```html
<!DOCTYPE html>
<html lang="en">
<head>
<meta charset="utf-8">
<title>Fen Athletics – Business Card</title>
<link href="https://fonts.googleapis.com/css2?family=Michroma&family=Saira:wght@400;600;800&display=swap" rel="stylesheet">
<style>
  :root {
    --page: #2b2b2d;
    --card: #0b0b0c;
    --card-edge: #161618;
    --red: #e3202a;
    --white: #ffffff;
    --silver: #c9cacc;
    --muted: #e8e8e8;
  }
  * { margin: 0; padding: 0; box-sizing: border-box; }
  html, body { width: 1200px; height: 900px; overflow: hidden; }
  body {
    background: var(--page);
    font-family: "Saira", sans-serif;
    position: relative;
  }
  .card {
    position: absolute;
    width: 620px;
    height: 350px;
    background: radial-gradient(ellipse at 50% 40%, var(--card-edge), var(--card) 70%);
    border-radius: 4px;
    box-shadow: 0 18px 40px rgba(0,0,0,.45);
    overflow: hidden;
  }
  .card--front { left: 140px; top: 70px; }
  .card--back  { left: 440px; top: 480px; }
  .card__stripe { position: absolute; inset: 0; width: 100%; height: 100%; }

  .wordmark {
    position: absolute;
    font-family: "Michroma", sans-serif;
    color: var(--silver);
    letter-spacing: 1px;
    white-space: nowrap;
    line-height: 1;
  }
  .card--front .wordmark { left: 60px; top: 52px; font-size: 36px; }
  .card--back .wordmark  { left: 0; right: 0; top: 60px; text-align: center; font-size: 54px; }

  .brands {
    position: absolute;
    left: 0; right: 0; top: 250px;
    display: flex; justify-content: center; gap: 26px;
    font-family: "Michroma", sans-serif;
    font-size: 10px;
    color: var(--muted);
  }
  .brand { display: flex; align-items: center; gap: 6px; }
  .brand__dot { width: 9px; height: 9px; border-radius: 50%; background: var(--red); }
  .site {
    position: absolute;
    left: 0; right: 0; top: 282px;
    text-align: center;
    font-weight: 800;
    font-size: 19px;
    color: var(--white);
  }
  .site__name { color: var(--red); }

  .contacts {
    position: absolute;
    right: 26px; top: 158px;
    list-style: none;
    text-align: right;
    font-size: 15px;
    line-height: 23px;
    color: var(--white);
  }
  .contacts li { display: flex; justify-content: flex-end; align-items: center; gap: 8px; }
  .contacts svg { width: 12px; height: 12px; flex: none; }

  .person {
    position: absolute;
    left: 28px; top: 256px;
    color: var(--white);
    font-size: 15px;
    line-height: 20px;
  }
  .person__name { font-weight: 800; font-size: 18px; line-height: 22px; }
  .person__role { color: var(--red); }
</style>
</head>
<body>

  <section class="card card--front" aria-label="Card front">
    <svg class="card__stripe" viewBox="0 0 620 350" aria-hidden="true">
      <line x1="0" y1="222" x2="232" y2="222" stroke="var(--red)" stroke-width="4"/>
      <polygon points="232,224 244,196 402,174 390,202" fill="var(--white)"/>
      <line x1="410" y1="124" x2="620" y2="124" stroke="var(--red)" stroke-width="4"/>
    </svg>
    <div class="wordmark">Fen Athletics</div>
    <div class="brands">
      <span class="brand"><span class="brand__dot"></span>TavaPuni</span>
      <span class="brand"><span class="brand__dot"></span>ElmStretch</span>
      <span class="brand"><span class="brand__dot"></span>Grit and Rain</span>
    </div>
    <div class="site">www.<span class="site__name">fenathletics</span>.co.uk</div>
  </section>

  <section class="card card--back" aria-label="Card back">
    <svg class="card__stripe" viewBox="0 0 620 350" aria-hidden="true">
      <line x1="0" y1="232" x2="222" y2="232" stroke="var(--red)" stroke-width="4"/>
      <polygon points="222,234 234,206 380,186 368,214" fill="var(--white)"/>
      <line x1="410" y1="112" x2="620" y2="112" stroke="var(--red)" stroke-width="4"/>
    </svg>
    <div class="wordmark">Fen</div>
    <ul class="contacts">
      <li>(+44) 1632 960 418
        <svg viewBox="0 0 12 12" aria-label="Phone"><circle cx="6" cy="6" r="6" fill="var(--red)"/><path d="M4 3l1.2 1.4-.6.8a4 4 0 0 0 2.2 2.2l.8-.6L9 8 8.2 9A5 5 0 0 1 3 3.8z" fill="var(--white)"/></svg>
      </li>
      <li>Leo@fenathletics.co.uk
        <svg viewBox="0 0 12 12" aria-label="Email"><circle cx="6" cy="6" r="6" fill="var(--red)"/><rect x="3" y="4" width="6" height="4.2" fill="none" stroke="var(--white)" stroke-width=".9"/><path d="M3 4l3 2.3L9 4" fill="none" stroke="var(--white)" stroke-width=".9"/></svg>
      </li>
      <li>www.fenathletics.co.uk
        <svg viewBox="0 0 12 12" aria-label="Website"><circle cx="6" cy="6" r="6" fill="var(--red)"/><circle cx="6" cy="6" r="3" fill="none" stroke="var(--white)" stroke-width=".9"/><path d="M3 6h6M6 3v6" stroke="var(--white)" stroke-width=".8"/></svg>
      </li>
    </ul>
    <div class="person">
      <div class="person__name">Leo Pemberton-Hale</div>
      <div class="person__role">Operations Manager</div>
      <div>Harrow Lane, Netherby</div>
      <div>Kelford, YO9 4QT</div>
    </div>
  </section>

</body>
</html>
```